Birchline Septic Solutions

Would like to see some single sided ones but would also like to see some double sided with one sided only being the logo. Owners name is Colin Vandro. Phone number is 555-214-0387
Services are pumping, inspections, installs, and repairs

Contact Information for Business Card

555-241-0387 Colin Vandro Larkmoor, OH

```html
<!DOCTYPE html>
<html lang="en">
<head>
<meta charset="utf-8">
<title>Birchline Septic Solutions – Business Card</title>
<link href="https://fonts.googleapis.com/css2?family=Montserrat:wght@500;600;700&display=swap" rel="stylesheet">
<style>
  :root {
    --backdrop: #e9e6e1;
    --card-frost: #eef0ef;
    --card-edge: #d6d2cc;
    --ink: #2a2b2d;
    --teal: #1a9e8c;
    --teal-deep: #137a6c;
    --teal-light: #22b7a6;
    --accent-line: #d9b8a6;
    --silver: #ecebe8;
  }
  * { margin: 0; padding: 0; box-sizing: border-box; }
  html, body {
    width: 1200px;
    height: 897px;
    overflow: hidden;
    background: var(--backdrop);
    font-family: "Montserrat", Arial, sans-serif;
  }
  .card {
    position: absolute;
    left: 75px;
    top: 148px;
    width: 1050px;
    height: 600px;
    border-radius: 26px;
    overflow: hidden;
    background: linear-gradient(160deg, #f6f7f6 0%, var(--card-frost) 55%, #e3e6e5 100%);
    box-shadow: 0 0 0 1px var(--card-edge), 0 18px 40px rgba(60, 50, 40, 0.18);
  }
  .card-band {
    position: absolute;
    inset: 0;
    width: 100%;
    height: 100%;
  }
  .brand {
    position: absolute;
    left: 52px;
    top: 150px;
    display: flex;
    align-items: center;
    gap: 18px;
    color: var(--ink);
  }
  .brand-mark {
    width: 22px;
    height: 22px;
    background: var(--teal-light);
  }
  .brand-name {
    font-weight: 700;
    font-size: 38px;
    line-height: 1.2;
    letter-spacing: 0.08em;
    text-transform: uppercase;
  }
  .contact {
    position: absolute;
    right: 48px;
    top: 395px;
    text-align: right;
    color: var(--silver);
  }
  .contact-name {
    font-weight: 700;
    font-size: 50px;
    letter-spacing: 0.02em;
    line-height: 1;
    text-transform: uppercase;
  }
  .contact-city {
    margin-top: 14px;
    font-weight: 600;
    font-size: 28px;
    line-height: 1;
  }
  .contact-phone {
    margin-top: 34px;
    font-weight: 500;
    font-size: 36px;
    line-height: 1;
    display: flex;
    align-items: center;
    justify-content: flex-end;
    gap: 8px;
  }
  .phone-icon { width: 32px; height: 28px; }
</style>
</head>
<body>
  <div class="card">
    <svg class="card-band" viewBox="0 0 1050 600" preserveAspectRatio="none" aria-hidden="true">
      <defs>
        <linearGradient id="teal-band" x1="0" y1="0" x2="1" y2="1">
          <stop offset="0" stop-color="#1d9f8a"/>
          <stop offset="0.6" stop-color="#17a69a"/>
          <stop offset="1" stop-color="#137a6c"/>
        </linearGradient>
      </defs>
      <path d="M0 470 C260 470 420 300 640 300 C820 300 930 330 1050 310 L1050 600 L0 600 Z" fill="url(#teal-band)"/>
      <path d="M0 455 C260 455 420 285 640 285 C820 285 930 315 1050 295" fill="none" stroke="var(--accent-line)" stroke-width="2"/>
    </svg>

    <div class="brand">
      <span class="brand-mark"></span>
      <span class="brand-name">Birchline<br>Septic Solutions</span>
    </div>

    <div class="contact">
      <p class="contact-name">Colin Vandro</p>
      <p class="contact-city">Larkmoor, OH</p>
      <p class="contact-phone">555-241-0387
        <svg class="phone-icon" viewBox="0 0 32 28" aria-hidden="true">
          <path d="M2 9 C2 3 30 3 30 9 L30 12 L23 12 L23 8 L9 8 L9 12 L2 12 Z" fill="currentColor"/>
          <path d="M8 13 L24 13 L28 26 L4 26 Z" fill="currentColor"/>
          <g fill="var(--teal)">
            <circle cx="12" cy="17" r="1.4"/><circle cx="16" cy="17" r="1.4"/><circle cx="20" cy="17" r="1.4"/>
            <circle cx="12" cy="21" r="1.4"/><circle cx="16" cy="21" r="1.4"/><circle cx="20" cy="21" r="1.4"/>
          </g>
        </svg>
      </p>
    </div>
  </div>
</body>
</html>
```